Business Card Design for Varomir Facility Services

We are looking for a Business Card Design for the Company "Varomir Facility Services."
Front side:
- Company Logo (small)
- Company Name, address, pohone, website and personal data.
- white background, for text e.g. company colors (blue or green like in the logo)
Please use following data:
Company data:
Varomir Facility Services Kostelac
Birkenhaldweg 14
6330 Cham
www.varomir-fs.ch
Person data:
Tarik Kostelac
Geschäftsführer
+41 76 519 47 83
info@varomir-fs.ch
Back side:
could be colored in blue or green
please use a big logo sing and some smaller icons to say what is all beeing offered in facility services, like cleaning, maintenance cleaning
industrial cleaning, caretaking, gardening, disposal. There is no need for everyone of the icons if there are similar or an icon is standing for more of them.
colors to use:
blue: HEX 246BB0
green: HEX 52B33E

```html
<!DOCTYPE html>
<html lang="de">
<head>
<meta charset="utf-8">
<title>Varomir Facility Services – Visitenkarte</title>
<link rel="stylesheet" href="https://fonts.googleapis.com/css2?family=Montserrat:wght@400;500;600&family=Roboto:wght@500&display=swap">
<style>
  :root {
    --brand-blue: #246BB0;
    --brand-green: #52B33E;
    --ink: #4a4a4a;
    --paper: #ffffff;
    --backdrop: #2b2b2b;
  }
  * { margin: 0; padding: 0; box-sizing: border-box; }
  html, body { width: 1200px; height: 900px; overflow: hidden; }
  body {
    background: var(--backdrop);
    position: relative;
    font-family: "Montserrat", sans-serif;
  }
  .card {
    position: absolute;
    left: 261px;
    width: 656px;
    height: 358px;
    overflow: hidden;
  }
  .card--front { top: 69px; background: var(--paper); }
  .card--back { top: 472px; background: var(--brand-blue); }

  .wordmark {
    position: absolute;
    font-family: "Montserrat", sans-serif;
    font-weight: 600;
    line-height: 1;
  }
  .wordmark__name { display: block; letter-spacing: 0.06em; }
  .wordmark__tagline { display: block; letter-spacing: 0.2em; }

  .card--front .wordmark { left: 25px; top: 88px; color: var(--brand-blue); }
  .card--front .wordmark__name { font-size: 32px; }
  .card--front .wordmark__tagline { font-size: 13.5px; margin-top: 8px; }

  .card--back .wordmark {
    left: 0; right: 0; top: 150px;
    text-align: center;
    color: var(--paper);
  }
  .card--back .wordmark__name { font-size: 50px; letter-spacing: 0.08em; }
  .card--back .wordmark__tagline { font-size: 20px; margin-top: 10px; letter-spacing: 0.22em; }

  .person {
    position: absolute;
    right: 27px;
    top: 167px;
    text-align: right;
  }
  .person__name {
    font-family: "Roboto", sans-serif;
    font-weight: 500;
    font-size: 25px;
    color: var(--brand-blue);
    line-height: 1;
  }
  .person__role {
    font-size: 17px;
    color: var(--ink);
    letter-spacing: 0.05em;
    margin-top: 7px;
  }
  .divider {
    position: absolute;
    left: 25px; right: 27px; top: 230px;
    height: 1.5px;
    background: var(--brand-blue);
  }
  .contact {
    position: absolute;
    left: 25px;
    top: 253px;
    list-style: none;
    font-size: 17px;
    color: var(--ink);
    letter-spacing: 0.04em;
  }
  .contact li { display: flex; align-items: center; height: 22px; }
  .contact svg { width: 11px; height: 11px; margin-right: 7px; fill: none; stroke: var(--brand-blue); stroke-width: 1.6; }
  .contact .accent { color: var(--brand-blue); font-weight: 500; }
  .address {
    position: absolute;
    right: 27px;
    top: 275px;
    text-align: right;
    font-size: 17px;
    line-height: 22px;
    color: var(--ink);
    letter-spacing: 0.04em;
    font-style: normal;
  }
  .footer-band { position: absolute; left: 0; bottom: 0; width: 656px; height: 30px; }
</style>
</head>
<body>

<section class="card card--front" aria-label="Vorderseite">
  <div class="wordmark">
    <span class="wordmark__name">VAROMIR</span>
    <span class="wordmark__tagline">FACILITY SERVICES</span>
  </div>

  <div class="person">
    <div class="person__name">Tarik Kostelac</div>
    <div class="person__role">Geschäftsführer</div>
  </div>

  <div class="divider"></div>

  <ul class="contact">
    <li>
      <svg viewBox="0 0 12 12"><path d="M3 1.5 L4.5 4 L3.5 5 Q4.5 7.5 7 8.5 L8 7.5 L10.5 9 L9.5 10.5 Q4 10 1.5 3 Z"/></svg>
      +41 76 519 47 83
    </li>
    <li>
      <svg viewBox="0 0 12 12"><rect x="1" y="2.5" width="10" height="7" rx="1"/><path d="M1.5 3 L6 6.5 L10.5 3"/></svg>
      info@varomir-fs.ch
    </li>
    <li>
      <svg viewBox="0 0 12 12"><circle cx="6" cy="6" r="4.8"/><ellipse cx="6" cy="6" rx="2" ry="4.8"/><path d="M1.2 6 H10.8 M2 3.5 H10 M2 8.5 H10"/></svg>
      <span>www.<span class="accent">varomir-fs</span>.ch</span>
    </li>
  </ul>

  <address class="address">
    Birkenhaldweg 14<br>
    6330 Cham
  </address>

  <svg class="footer-band" viewBox="0 0 656 30" preserveAspectRatio="none" aria-hidden="true">
    <path d="M0 20 H362 C384 20 392 2 418 0 H656 V30 H0 Z" fill="var(--brand-blue)"/>
    <path d="M0 8 H368 Q376 8 384 5.5 L386 8.5 Q377 13 368 13 H0 Z" fill="var(--brand-green)"/>
  </svg>
</section>

<section class="card card--back" aria-label="Rückseite">
  <div class="wordmark">
    <span class="wordmark__name">VAROMIR</span>
    <span class="wordmark__tagline">FACILITY SERVICES</span>
  </div>
</section>

</body>
</html>
```